Landing Page Design for Adult Dating Age Verification (18+)

The objective of this task is to design a visually appealing pre-landing page for the adult dating site "Quillmera (site: https://quillmera.com/)" with an age verification mechanism. The pre-landing page will feature two buttons that redirect visitors to the main offer. The design should also include a footer block that includes links to the terms of use, privacy policy, and contact us pages.

Design Requirements:
Develop an age verification section prominently displayed on the pre-landing page.
Design the section to include two buttons labeled "Yes" and "No" for visitors to confirm their age.
Ensure the section is visually appealing and clearly communicates the purpose of age verification.

Visual Appeal:
Create a visually appealing design that aligns with the branding and theme of the "Quillmera" adult dating site.
Use suitable color schemes, typography, and graphics to enhance the overall visual appeal of the pre-landing page.

Layout and Navigation:
Design an engaging and intuitive layout that encourages visitors to interact with the page and proceed to the main offer.
Ensure clear and visible navigation elements that direct visitors to the main offer or provide additional information.

Responsive Design:
Develop a responsive design that provides a seamless user experience across various devices, including desktop and mobile.
Ensure the design elements and layout adapt well to different screen sizes and resolutions.

File Formats and Assets:
Deliver the final design in PSD, AI, or Sketch format, ensuring that the files are well-organized and layered.
Include any necessary images or assets used in the design, ensuring they are of high quality and optimized for web use.

```html
<!DOCTYPE html>
<html lang="en">
<head>
<meta charset="utf-8">
<title>Quillmera — Age Verification</title>
<link rel="stylesheet" href="https://fonts.googleapis.com/css2?family=Poppins:wght@400;500;600&family=Kalam:wght@300;400&display=swap">
<style>
  :root {
    --footer-bg: #14003a;
    --brand-lilac: #d5b6dc;
    --pill-purple: #7b2480;
    --yes-purple: #7a2a86;
    --no-red: #f2162f;
    --text-light: #ffffff;
    --card-edge: rgba(255,255,255,0.14);
    --card-fill: rgba(40,20,25,0.28);
  }
  * { margin: 0; padding: 0; box-sizing: border-box; }
  html, body { width: 1200px; height: 991px; overflow: hidden; }
  body { font-family: "Poppins", sans-serif; color: var(--text-light); background: var(--footer-bg); position: relative; }

  .hero {
    position: absolute; left: 0; top: 0; width: 1200px; height: 733px;
    background:
      radial-gradient(ellipse 420px 300px at 780px 320px, rgba(150,100,85,0.55), transparent 70%),
      radial-gradient(ellipse 260px 380px at 120px 460px, rgba(120,120,110,0.35), transparent 70%),
      linear-gradient(160deg, #2c1b1e 0%, #4a2f2c 40%, #3a2426 70%, #24161b 100%);
  }

  .site-header { position: absolute; top: 0; left: 0; width: 1200px; height: 110px; }
  .brand { position: absolute; display: flex; align-items: center; gap: 14px; }
  .brand-mark { width: 54px; height: 54px; border-radius: 50%; background: var(--brand-lilac); }
  .brand-name { font-family: "Poppins", sans-serif; font-weight: 600; color: var(--text-light); }
  .site-header .brand { left: 440px; top: 26px; }
  .site-header .brand-name { font-size: 44px; line-height: 54px; }

  .nav-signin {
    position: absolute; left: 820px; top: 38px; width: 95px; height: 34px;
    border-radius: 17px; background: var(--pill-purple);
    font-size: 17px; line-height: 34px; text-align: center;
  }
  .nav-join { position: absolute; left: 944px; top: 41px; font-size: 17px; line-height: 28px; }
  .nav-lang { position: absolute; left: 1067px; top: 41px; font-size: 17px; line-height: 28px; display: flex; align-items: center; gap: 4px; }

  .age-card {
    position: absolute; left: 328px; top: 287px; width: 548px; height: 279px;
    border: 2px solid var(--card-edge); border-radius: 34px; background: var(--card-fill);
    text-align: center;
  }
  .age-card__art { position: absolute; left: 220px; top: 10px; width: 108px; height: 48px; border-radius: 8px; background: rgba(170,110,110,0.18); }
  .age-card__lead { position: absolute; left: 0; width: 100%; top: 60px; font-family: "Kalam", cursive; font-weight: 300; font-size: 25px; }
  .age-card__question { position: absolute; left: 0; width: 100%; top: 85px; font-family: "Kalam", cursive; font-weight: 300; font-size: 46px; line-height: 60px; }
  .heart-btn { position: absolute; top: 146px; width: 86px; height: 74px; }
  .heart-btn svg { position: absolute; inset: 0; }
  .heart-btn span { position: relative; display: block; font-family: "Kalam", cursive; font-size: 23px; line-height: 60px; }
  .heart-btn--yes { left: 146px; }
  .heart-btn--no { left: 291px; }

  .site-footer { position: absolute; left: 0; top: 733px; width: 1200px; height: 258px; background: var(--footer-bg); }
  .site-footer .brand { left: 494px; top: 49px; gap: 10px; }
  .site-footer .brand-mark { width: 44px; height: 44px; }
  .site-footer .brand-name { font-size: 30px; line-height: 44px; }
  .footer-links a { position: absolute; top: 145px; color: var(--text-light); text-decoration: none; font-size: 20px; line-height: 28px; border-bottom: 1px solid var(--text-light); }
  .link-terms { left: 373px; }
  .link-privacy { left: 537px; }
  .link-contact { left: 713px; padding-left: 6px; }
  .copyright { position: absolute; left: 0; width: 100%; top: 204px; text-align: center; font-size: 19px; }
</style>
</head>
<body>
  <div class="hero" role="img" aria-label="Dim romantic photo of a couple embracing"></div>

  <header class="site-header">
    <div class="brand"><span class="brand-mark"></span><span class="brand-name">Quillmera</span></div>
    <div class="nav-signin">Sign in</div>
    <div class="nav-join">Join Now</div>
    <div class="nav-lang">English
      <svg width="18" height="12" viewBox="0 0 18 12"><path d="M2 2 L9 9 L16 2" fill="none" stroke="#fff" stroke-width="2"/></svg>
    </div>
  </header>

  <section class="age-card">
    <div class="age-card__art" role="img" aria-label="Faint line drawing of a reclining figure"></div>
    <p class="age-card__lead">Are You over</p>
    <h1 class="age-card__question">18 Years Of Age?</h1>
    <div class="heart-btn heart-btn--yes">
      <svg viewBox="0 0 86 74" width="86" height="74"><path d="M43 72 C20 52 2 40 2 20 C2 8 12 1 24 1 C33 1 40 7 43 14 C46 7 53 1 62 1 C74 1 84 8 84 20 C84 40 66 52 43 72 Z" fill="var(--yes-purple)" stroke="rgba(0,0,0,0.35)" stroke-width="1.5"/></svg>
      <span>Yes</span>
    </div>
    <div class="heart-btn heart-btn--no">
      <svg viewBox="0 0 88 74" width="88" height="74"><path d="M44 72 C20 52 2 40 2 20 C2 8 12 1 24 1 C33 1 40 7 44 14 C48 7 55 1 64 1 C76 1 86 8 86 20 C86 40 68 52 44 72 Z" fill="var(--no-red)"/><path d="M44 14 L40 30 L48 40 L40 58" fill="none" stroke="#7a0010" stroke-width="1.5"/></svg>
      <span>No</span>
    </div>
  </section>

  <footer class="site-footer">
    <div class="brand"><span class="brand-mark"></span><span class="brand-name">Quillmera</span></div>
    <nav class="footer-links">
      <a class="link-terms" href="https://quillmera.com/">Terms of Use</a>
      <a class="link-privacy" href="https://quillmera.com/">Privacy Policy</a>
      <a class="link-contact" href="https://quillmera.com/">Contact Us</a>
    </nav>
    <p class="copyright">@2023 Copyrights Quillmera All Right Reserved</p>
  </footer>
</body>
</html>
```